Fabrication and machining company needing printed material designs.

Heron Vessels, Inc. wants to use appealing visuals as well as informative text to tell potential clients about our capabilities in fabrication and machining. We have a new logo to showcase as well as a new website. The use of print media will allow us to leave tangible information with clients, and therefore the design will need to be concise, informative, and visually appealing.

Full Page Flyer (approx. 8.5" x 11"), front and back design. This will be a detailed offering of capabilities and services for our shop.

Half Page Flyer (approx. 5.5" x 8.5"), front and back design. An abbreviated version of the full page flyer, meant to be easily handed out and stored inside a note book.

Bi-fold business card front and back. General offerings of our services. Minimal if any details. Finished size is twice the size of a business card (approx. 4" x 3.5"), once folded in half will be the same size as a standard business card (approx. 2" x 3.5").

Please use www.heronvesselsinc.example for theme ideas. The font used for our logo is ethnocentric, not to be used for all text.

Target Market(s)

Industrial Consumers

Font styles to use
Sans Serif

```html
<!DOCTYPE html>
<html lang="en">
<head>
<meta charset="utf-8">
<title>Heron Vessels, Inc. — Print Collateral</title>
<link rel="stylesheet" href="https://fonts.googleapis.com/css2?family=Montserrat:wght@400;500;600;700;800&family=Orbitron:wght@700;800;900&display=swap">
<style>
:root{
  --orange:#f26a21;
  --orange-deep:#d9551a;
  --ink:#111111;
  --dark:#1c1c1c;
  --char:#2a2a2a;
  --grey:#6d6e70;
  --grey-mid:#9a9b9d;
  --light:#e4e4e4;
  --paper:#ffffff;
  --board:#e8e2d6;
  --display:"Orbitron",sans-serif;
  --text:"Montserrat",sans-serif;
}
*{box-sizing:border-box;margin:0;padding:0}
html,body{width:1200px;height:3000px;overflow:hidden}
body{background:var(--board);font-family:var(--text);color:var(--ink)}
.canvas{position:relative;width:1200px;height:3000px}

/* ---------- placement on the board ---------- */
.slot{position:absolute}
.slot--full-front{left:40px;top:80px}
.slot--full-back{left:620px;top:80px}
.slot--half-front{left:70px;top:910px}
.slot--half-back{left:650px;top:910px}
.slot--card-out{left:40px;top:1830px}
.slot--card-in{left:700px;top:1830px}
.board-label{position:absolute;font:400 20px/1 var(--text);color:#5d5a55;letter-spacing:.02em;text-align:center;width:540px}
.label--full-front{left:40px;top:800px}
.label--full-back{left:620px;top:800px}
.label--half-front{left:40px;top:1675px}
.label--half-back{left:620px;top:1675px}
.label--card-out{left:-0px;top:2262px}
.label--card-in{left:660px;top:2262px}
.label--card{left:330px;top:2022px;width:540px}

/* ---------- shared pieces ---------- */
.brand{font:800 1.3em/1 var(--text);color:var(--ink);letter-spacing:.04em;text-transform:uppercase;white-space:nowrap}
.brand--light{color:var(--paper)}
.photo{display:block}
.tick-list{list-style:none}
.tick-list li{position:relative;padding-left:1.9em;margin-bottom:.55em;line-height:1.15}
.tick-list li::before{content:"";position:absolute;left:0;top:.05em;width:1.05em;height:1.05em;border:1px solid var(--orange);border-radius:50%}
.tick-list li::after{content:"";position:absolute;left:.33em;top:.25em;width:.3em;height:.5em;border:solid var(--orange);border-width:0 1.5px 1.5px 0;transform:rotate(45deg)}

/* ---------- flyer frame ---------- */
.flyer{position:relative;background:var(--paper);overflow:hidden;display:flex;flex-direction:column;box-shadow:0 2px 6px rgba(0,0,0,.15)}
.flyer--full{width:540px;height:699px;font-size:10px}
.flyer--half{width:480px;height:742px;font-size:9px}

.flyer-head{flex:0 0 10%;display:flex;align-items:center;padding-left:6%;background:var(--paper)}

.hero{position:relative;flex:0 0 27%;background:var(--ink)}
.hero-photo{position:absolute;inset:0;background:
  radial-gradient(ellipse 30% 40% at 68% 52%,rgba(255,150,60,.85),rgba(242,106,33,.35) 45%,transparent 75%),
  linear-gradient(100deg,#0d0d0d 0%,#1a1410 45%,#3a2418 70%,#140f0c 100%)}
.hero-title{position:absolute;left:6%;top:26%;font-family:var(--display);font-weight:800;font-size:2.3em;line-height:1.15;letter-spacing:.04em;color:var(--paper)}
.hero-title span{display:block}
.hero-title .t-orange{color:var(--orange)}

.cert-seal{position:absolute;left:6%;top:22%;width:20%;aspect-ratio:1;border-radius:50%;background:radial-gradient(circle at 50% 40%,#3a3a3a,#111 70%);border:.35em solid var(--paper);box-shadow:0 0 0 .15em var(--grey-mid);z-index:3}

.band{position:relative;flex:0 0 5.5%;background:linear-gradient(90deg,var(--light),#f4f4f4)}
.band-fill{position:absolute;left:30%;right:0;top:0;bottom:0;background:var(--orange);clip-path:polygon(4% 0,100% 0,100% 100%,0 100%);display:flex;align-items:center;justify-content:center}
.band-fill h2{font:800 1.9em/1 var(--display);color:var(--paper);letter-spacing:.12em}

.cap-grid{flex:1;display:grid;grid-template-columns:32% 34% 34%;padding:5.5% 4% 0 5%;background:linear-gradient(180deg,#fff 0%,#f2f2f2 100%);column-gap:1%;min-height:0}
.cap{margin-bottom:.55em}
.cap h3{font:700 1.02em/1.05 var(--text);color:var(--orange);text-transform:uppercase;letter-spacing:.01em}
.cap p{font:500 .68em/1.3 var(--text);color:var(--grey)}
.cap-photo{height:7.5em;margin-top:.6em;border:.25em solid var(--paper);box-shadow:0 1px 3px rgba(0,0,0,.3);background:linear-gradient(120deg,#2b2b2b,#9ea3a8 45%,#50555a 70%,#1d1d1d)}
.special-box{background:var(--light);border-radius:.4em;padding:.7em .8em .8em;margin-bottom:1em}
.special-box h4{display:inline-block;background:var(--orange);color:var(--paper);font:700 .9em/1 var(--text);padding:.35em 1.1em;margin:-.2em 0 .8em -1.2em;letter-spacing:.04em}
.special-box .tick-list{font:600 .78em/1.1 var(--text);color:#3a3a3a}
.special-box .tick-list li{margin-bottom:.7em}

.flyer-foot{flex:0 0 6.5%;background:var(--ink);display:flex;align-items:center;justify-content:flex-end;gap:3.5em;padding-right:4%}
.call small{display:block;font:600 .62em/1 var(--text);color:var(--orange);letter-spacing:.06em}
.call strong{font:600 1.3em/1.1 var(--text);color:var(--paper)}
.contact{font:500 .65em/1.5 var(--text);color:var(--paper)}
.contact span{display:flex;align-items:center;gap:.5em}
.contact svg{width:1em;height:1em;fill:var(--orange)}
.dot{display:inline-block;width:.55em;height:.55em;border-radius:50%;background:var(--orange)}

/* ---------- flyer back ---------- */
.markets{position:relative;flex:0 0 38%;background:var(--ink)}
.markets-photo{position:absolute;left:0;top:0;bottom:0;width:48%;background:
  radial-gradient(ellipse 25% 25% at 55% 60%,rgba(255,170,80,.8),transparent 70%),
  linear-gradient(110deg,#20252b,#39414a 40%,#1c1f24 75%,#111)}
.market-map{position:absolute;left:44%;right:2%;top:6%;bottom:8%}
.market-map svg.arc{position:absolute;inset:0;width:100%;height:100%}
.node{position:absolute;display:flex;flex-direction:column;align-items:center;transform:translate(-50%,-50%);font:700 .55em/1.15 var(--text);color:var(--paper);text-align:center;text-transform:uppercase;gap:.4em}
.node i{display:block;width:2.6em;height:2.6em;border:1.5px solid var(--paper);border-radius:50%;background:var(--ink);position:relative}
.node i::after{content:"";position:absolute;inset:28%;border-radius:50%;background:var(--paper)}
.node--oil{left:20%;top:24%;flex-direction:row}
.node--power{left:88%;top:16%}
.node--water{left:36%;top:62%}
.node--aggregate{left:86%;top:58%}
.node--mining{left:62%;top:86%}
.tank-block{position:absolute;left:40%;top:14%;width:34%;text-align:center}
.tank-art{height:4.3em;background:linear-gradient(180deg,#d9dadb,#8d9096 60%,#4d5055)}
.tank-block span{display:block;margin-top:.4em;font:800 .7em/1 var(--text);color:var(--paper);letter-spacing:.04em}

.product{position:relative;flex:1;background:var(--paper)}
.product-side{position:absolute;right:0;top:0;bottom:0;width:34%;background:linear-gradient(160deg,var(--orange),var(--orange-deep))}
.side-title{position:absolute;right:-14%;top:50%;transform:translate(0,-50%) rotate(-90deg);font:800 1.9em/1.1 var(--display);color:var(--paper);white-space:nowrap;letter-spacing:.04em;text-align:center}
.product-copy{position:absolute;left:0;top:0;bottom:0;width:50%;padding:5% 0 0 7%}
.product-copy h2{font:400 1.8em/1 var(--text);color:var(--grey);letter-spacing:.02em;padding-bottom:.6em;border-bottom:2px solid var(--light);margin-bottom:1em}
.product-copy h2 b{font-weight:600;color:var(--orange)}
.product-copy .tick-list{font:600 .95em/1.1 var(--text);color:#333;text-transform:uppercase;letter-spacing:.02em}
.product-copy .tick-list li{margin-bottom:.95em}
.cert-strip{display:flex;gap:.5em;background:var(--light);padding:.45em .6em;margin:.9em 0 1.3em}
.cert-strip i{flex:1;height:1em;border-radius:.5em;background:#c9c9c9}
.idea h3{font:700 .85em/1.2 var(--text);color:var(--orange);text-transform:uppercase}
.idea p{font:500 .66em/1.35 var(--text);color:var(--grey);margin-top:.5em}
.product-copy .brand{display:block;margin-top:1.6em;font-size:1.05em}
.product-photos{position:absolute;right:22%;top:4%;width:24%;display:flex;flex-direction:column;gap:4%;height:90%}
.product-photos .photo{flex:1;border:.3em solid var(--paper);box-shadow:0 1px 4px rgba(0,0,0,.35)}
.ph-fittings{background:linear-gradient(135deg,#e9eaeb,#9a9ea3 50%,#54585d)}
.ph-pipes{background:linear-gradient(135deg,#3a2a1e,#b87a4b 40%,#2b2b2b)}
.ph-flange{background:linear-gradient(135deg,#c9ccd0,#7b8086 55%,#3f4246)}
.flyer-back .flyer-foot{justify-content:flex-end}

/* ---------- bi-fold card ---------- */
.card{position:relative;width:460px;height:402px;font-size:7px;display:grid;grid-template-columns:1fr 1fr;background:var(--paper);overflow:hidden;box-shadow:0 2px 6px rgba(0,0,0,.15)}
.card-panel{position:relative;overflow:hidden}
.panel--black{background:var(--ink)}
.card-foot{position:absolute;left:7%;right:5%;bottom:6%}
.card-foot .brand{font-size:1.3em;display:block;margin-bottom:1.6em}
.card-foot .row{display:flex;gap:2.5em;align-items:flex-end}
.card-foot .call strong{font-size:1.2em}
.panel--cover{display:flex;align-items:center;justify-content:center}
.panel--cover .brand{font-size:2.2em;margin-top:-8%}
.cover-base{position:absolute;left:0;right:0;bottom:0;height:26%;background:linear-gradient(180deg,rgba(255,255,255,0),#d8d8d8 70%,#bfbfbf)}
.cover-stripes{position:absolute;left:0;right:0;bottom:4%;height:4%}
.cover-stripes::before{content:"";position:absolute;left:0;right:0;top:0;height:35%;background:var(--orange)}
.cover-stripes::after{content:"";position:absolute;left:0;right:0;bottom:0;height:35%;background:var(--grey)}

.card-inside{padding:0}
.inside-left{padding:6% 5% 5% 6%;border-right:1px solid #eee}
.inside-left h2{font:700 1.5em/1 var(--text);color:var(--orange);text-transform:uppercase;padding-bottom:.5em;border-bottom:1px solid var(--light);margin-bottom:1.1em}
.mini-cols{display:grid;grid-template-columns:1fr 1fr;column-gap:.8em;font:600 .7em/1.15 var(--text);color:#333;text-transform:uppercase}
.mini-cols li{margin-bottom:.5em;padding-left:1.8em}
.inside-lower{display:grid;grid-template-columns:55% 40%;gap:5%;margin-top:1.6em}
.inside-lower .special-box{font-size:1em;padding:.6em .7em}
.inside-lower .special-box .tick-list{font-size:.75em}
.inside-lower .special-box .tick-list li{margin-bottom:.55em}
.inside-photos{display:flex;flex-direction:column;gap:.9em}
.inside-photos .photo{height:7.5em;border:.25em solid var(--paper);box-shadow:0 1px 3px rgba(0,0,0,.3)}
.ph-sparks{background:radial-gradient(ellipse 40% 40% at 55% 50%,rgba(255,140,50,.8),transparent 70%),#1a1410}
.ph-weld{background:radial-gradient(ellipse 35% 35% at 40% 60%,rgba(255,170,80,.7),transparent 70%),linear-gradient(110deg,#20252b,#39414a)}
.inside-right{padding:6% 6% 5% 6%}
.inside-right h2{font:400 1.5em/1 var(--text);color:var(--grey);padding-bottom:.5em;border-bottom:1px solid var(--light);margin-bottom:1.1em}
.inside-right h2 b{font-weight:600;color:var(--orange)}
.inside-right .tick-list{font:600 .75em/1.1 var(--text);text-transform:uppercase;color:#333}
.inside-right .cert-strip{margin:.9em 0 1em}
.inside-right .idea h3{font-size:.95em}
.inside-right .idea p{font-size:.7em}
.inside-pair{display:flex;gap:1em;margin-top:1.2em}
.inside-pair .photo{flex:1;height:6.4em;border:.25em solid var(--paper);box-shadow:0 1px 3px rgba(0,0,0,.3)}
.inside-sign{position:absolute;left:6%;right:6%;bottom:5%;display:flex;justify-content:space-between;align-items:flex-end}
.inside-sign .brand{font-size:1.1em}
.inside-sign small{font:500 .75em/1 var(--text);color:var(--grey)}
</style>
</head>
<body>
<main class="canvas">

<!-- ===== Full page flyer, front ===== -->
<div class="slot slot--full-front">
<article class="flyer flyer--full">
  <header class="flyer-head"><span class="brand">Heron Vessels, Inc.</span></header>
  <section class="hero">
    <div class="hero-photo photo" role="img" aria-label="Laser cutting head throwing sparks across a steel plate"></div>
    <h1 class="hero-title"><span class="t-orange">FABRICATION</span><span>AND MACHINING</span></h1>
  </section>
  <div class="cert-seal" role="img" aria-label="Certification seal"></div>
  <div class="band"><div class="band-fill"><h2>CAPABILITIES</h2></div></div>
  <div class="cap-grid">
    <div class="cap-col">
      <div class="cap"><h3>Horizontal Lathes</h3><p>Up To 24" Dia &amp; 10' Long</p></div>
      <div class="cap"><h3>Vertical Lathes</h3><p>Up To 44" Dia</p></div>
      <div class="cap"><h3>Horizontal Boring Mill Capabilities</h3></div>
      <div class="cap"><h3>Press Brake</h3><p>1" Plate x 5' Wide<br>3/8" Plate x 14' Wide</p></div>
      <div class="cap"><h3>Iron Workers</h3><p>Up To 85 Tons</p></div>
      <div class="cap"><h3>Band Saws</h3><p>22" Cut Capacity</p></div>
      <div class="cap"><h3>CNC Plasma Cutting</h3><p>8' X 20' Capacity</p></div>
      <div class="cap"><h3>CNC Roll Forming</h3><p>1/2" X 10' Capacity</p></div>
      <div class="cap-photo photo" role="img" aria-label="Machined steel shaft turning on a lathe"></div>
    </div>
    <div class="cap-col">
      <div class="cap"><h3>Facility</h3><p>35,000 ft2 Facility<br>5 Acre Storage Yard</p></div>
      <div class="cap"><h3>Design &amp; Engineering</h3><p>CAD Drawings<br>Engineering Services<br>3D Modeling</p></div>
      <div class="cap"><h3>Welding Processes</h3><p>Carbon Steel<br>Stainless Steel<br>Aluminum</p></div>
      <div class="cap"><h3>Paint &amp; Corrosion Control</h3><p>Dedicated Paint Bay<br>Plural Component Application Equip<br>Multi Step Liner Systems<br>Stainless Steel Passivation<br>Powder Coating<br>Galvanizing</p></div>
      <div class="cap"><h3>Sandblasting</h3><p>High Production Capacity</p></div>
      <div class="cap"><h3>Insulating Systems</h3><p>Polyurethane Spray Foam<br>Metal Wrap<br>Heat Trace</p></div>
    </div>
    <div class="cap-col">
      <div class="special-box">
        <h4>SPECIALTIES</h4>
        <ul class="tick-list">
          <li>Tanks</li><li>Piping</li><li>Firetubes</li><li>Walkways &amp; Stairs</li><li>Pump Skids</li><li>Trailer Components</li><li>Tank Vents Clarifiers</li>
        </ul>
      </div>
      <div class="cap"><h3>Hydraulic Assemblies</h3><p>System Testing<br>Hose Assemblies<br>Ram Rebuilding</p></div>
      <div class="cap"><h3>Drivelines</h3><p>Custom built<br>Rebuilding<br>Straightening</p></div>
    </div>
  </div>
  <footer class="flyer-foot">
    <div class="call"><small>CALL US NOW</small><strong>555-014-2270</strong></div>
    <div class="contact">
      <span><svg viewBox="0 0 10 10"><path d="M5 0a3.5 3.5 0 0 0-3.5 3.5C1.5 6 5 10 5 10s3.5-4 3.5-6.5A3.5 3.5 0 0 0 5 0zm0 5a1.5 1.5 0 1 1 0-3 1.5 1.5 0 0 1 0 3z"/></svg>410 North Ridge Rd Ashford, UT 84000</span>
      <span><i class="dot"></i>www.heronvesselsinc.example</span>
    </div>
  </footer>
</article>
</div>

<!-- ===== Full page flyer, back ===== -->
<div class="slot slot--full-back">
<article class="flyer flyer--full flyer-back">
  <section class="markets">
    <div class="markets-photo photo" role="img" aria-label="Welder at work in smoke and sparks"></div>
    <div class="market-map">
      <svg class="arc" viewBox="0 0 100 100" preserveAspectRatio="none"><path d="M20 24 Q55 -5 88 16 Q100 40 86 58 Q78 84 62 86 Q42 84 36 62 Q24 46 20 24" fill="none" stroke="#fff" stroke-width=".5" stroke-dasharray="1.5 1.5" vector-effect="non-scaling-stroke"/></svg>
      <div class="tank-block"><div class="tank-art photo" role="img" aria-label="Row of storage tanks"></div><span>HERON VESSELS</span></div>
      <div class="node node--oil"><span>Oil &amp; Gas</span><i></i></div>
      <div class="node node--power"><i></i><span>Power<br>Generation</span></div>
      <div class="node node--water"><i></i><span>Water &amp;<br>Waste Water</span></div>
      <div class="node node--aggregate"><i></i><span>Aggregate</span></div>
      <div class="node node--mining"><i></i><span>Mining</span></div>
    </div>
  </section>
  <section class="product">
    <div class="product-side"><p class="side-title">FABRICATION<br>AND MACHINING</p></div>
    <div class="product-copy">
      <h2>OUR <b>PRODUCT</b></h2>
      <ul class="tick-list">
        <li>Tanks</li><li>Piping</li><li>Machining</li><li>Walkway &amp; Stairs</li><li>Tank Liner Systems</li><li>Insulation</li>
      </ul>
      <div class="cert-strip"><i></i><i></i><i></i><i></i></div>
      <div class="idea">
        <h3>A brilliant idea materialized...</h3>
        <p>It is said great ideas start with a brilliant flash. Likewise, we think a brilliant solution starts with an arc. From concept to construction we deliver results for the long haul.</p>
      </div>
      <span class="brand">Heron Vessels, Inc.</span>
    </div>
    <div class="product-photos">
      <div class="photo ph-fittings" role="img" aria-label="Stack of stainless pipe fittings"></div>
      <div class="photo ph-pipes" role="img" aria-label="Fabricated pipe sections in the shop"></div>
      <div class="photo ph-flange" role="img" aria-label="Machined steel flange"></div>
    </div>
  </section>
  <footer class="flyer-foot">
    <div class="call"><small>CALL US NOW</small><strong>555-014-2270</strong></div>
    <div class="contact">
      <span><svg viewBox="0 0 10 10"><path d="M5 0a3.5 3.5 0 0 0-3.5 3.5C1.5 6 5 10 5 10s3.5-4 3.5-6.5A3.5 3.5 0 0 0 5 0zm0 5a1.5 1.5 0 1 1 0-3 1.5 1.5 0 0 1 0 3z"/></svg>410 North Ridge Rd Ashford, UT 84000</span>
      <span><i class="dot"></i>www.heronvesselsinc.example</span>
    </div>
  </footer>
</article>
</div>

<!-- ===== Half page flyer, front ===== -->
<div class="slot slot--half-front">
<article class="flyer flyer--half">
  <header class="flyer-head"><span class="brand">Heron Vessels, Inc.</span></header>
  <section class="hero">
    <div class="hero-photo photo" role="img" aria-label="Laser cutting head throwing sparks across a steel plate"></div>
    <h1 class="hero-title"><span class="t-orange">FABRICATION</span><span>AND MACHINING</span></h1>
  </section>
  <div class="cert-seal" role="img" aria-label="Certification seal"></div>
  <div class="band"><div class="band-fill"><h2>CAPABILITIES</h2></div></div>
  <div class="cap-grid">
    <div class="cap-col">
      <div class="cap"><h3>Horizontal Lathes</h3><p>Up To 24" Dia &amp; 10' Long</p></div>
      <div class="cap"><h3>Vertical Lathes</h3><p>Up To 44" Dia</p></div>
      <div class="cap"><h3>Horizontal Boring Mill Capabilities</h3></div>
      <div class="cap"><h3>Press Brake</h3><p>1" Plate x 5' Wide<br>3/8" Plate x 14' Wide</p></div>
      <div class="cap"><h3>Iron Workers</h3><p>Up To 85 Tons</p></div>
      <div class="cap"><h3>Band Saws</h3><p>22" Cut Capacity</p></div>
      <div class="cap"><h3>CNC Plasma Cutting</h3><p>8' X 20' Capacity</p></div>
      <div class="cap"><h3>CNC Roll Forming</h3><p>1/2" X 10' Capacity</p></div>
      <div class="cap-photo photo" role="img" aria-label="Machined steel shaft turning on a lathe"></div>
    </div>
    <div class="cap-col">
      <div class="cap"><h3>Facility</h3><p>35,000 ft2 Facility<br>5 Acre Storage Yard</p></div>
      <div class="cap"><h3>Design &amp; Engineering</h3><p>CAD Drawings<br>Engineering Services<br>3D Modeling</p></div>
      <div class="cap"><h3>Welding Processes</h3><p>Carbon Steel<br>Stainless Steel<br>Aluminum</p></div>
      <div class="cap"><h3>Paint &amp; Corrosion Control</h3><p>Dedicated Paint Bay<br>Plural Component Application Equip<br>Multi Step Liner Systems<br>Stainless Steel Passivation<br>Powder Coating<br>Galvanizing</p></div>
      <div class="cap"><h3>Sandblasting</h3><p>High Production Capacity</p></div>
      <div class="cap"><h3>Insulating Systems</h3><p>Polyurethane Spray Foam<br>Metal Wrap<br>Heat Trace</p></div>
    </div>
    <div class="cap-col">
      <div class="special-box">
        <h4>SPECIALTIES</h4>
        <ul class="tick-list">
          <li>Tanks</li><li>Piping</li><li>Firetubes</li><li>Walkways &amp; Stairs</li><li>Pump Skids</li><li>Trailer Components</li><li>Tank Vents Clarifiers</li>
        </ul>
      </div>
      <div class="cap"><h3>Hydraulic Assemblies</h3><p>System Testing<br>Hose Assemblies<br>Ram Rebuilding</p></div>
      <div class="cap"><h3>Drivelines</h3><p>Custom built<br>Rebuilding<br>Straightening</p></div>
    </div>
  </div>
  <footer class="flyer-foot">
    <div class="call"><small>CALL US NOW</small><strong>555-014-2270</strong></div>
    <div class="contact">
      <span><svg viewBox="0 0 10 10"><path d="M5 0a3.5 3.5 0 0 0-3.5 3.5C1.5 6 5 10 5 10s3.5-4 3.5-6.5A3.5 3.5 0 0 0 5 0zm0 5a1.5 1.5 0 1 1 0-3 1.5 1.5 0 0 1 0 3z"/></svg>410 North Ridge Rd Ashford, UT 84000</span>
      <span><i class="dot"></i>www.heronvesselsinc.example</span>
    </div>
  </footer>
</article>
</div>

<!-- ===== Half page flyer, back ===== -->
<div class="slot slot--half-back">
<article class="flyer flyer--half flyer-back">
  <section class="markets">
    <div class="markets-photo photo" role="img" aria-label="Welder at work in smoke and sparks"></div>
    <div class="market-map">
      <svg class="arc" viewBox="0 0 100 100" preserveAspectRatio="none"><path d="M20 24 Q55 -5 88 16 Q100 40 86 58 Q78 84 62 86 Q42 84 36 62 Q24 46 20 24" fill="none" stroke="#fff" stroke-width=".5" stroke-dasharray="1.5 1.5" vector-effect="non-scaling-stroke"/></svg>
      <div class="tank-block"><div class="tank-art photo" role="img" aria-label="Row of storage tanks"></div><span>HERON VESSELS</span></div>
      <div class="node node--oil"><span>Oil &amp; Gas</span><i></i></div>
      <div class="node node--power"><i></i><span>Power<br>Generation</span></div>
      <div class="node node--water"><i></i><span>Water &amp;<br>Waste Water</span></div>
      <div class="node node--aggregate"><i></i><span>Aggregate</span></div>
      <div class="node node--mining"><i></i><span>Mining</span></div>
    </div>
  </section>
  <section class="product">
    <div class="product-side"><p class="side-title">FABRICATION<br>AND MACHINING</p></div>
    <div class="product-copy">
      <h2>OUR <b>PRODUCT</b></h2>
      <ul class="tick-list">
        <li>Tanks</li><li>Piping</li><li>Machining</li><li>Walkway &amp; Stairs</li><li>Tank Liner Systems</li><li>Insulation</li>
      </ul>
      <div class="cert-strip"><i></i><i></i><i></i><i></i></div>
      <div class="idea">
        <h3>A brilliant idea materialized...</h3>
        <p>It is said great ideas start with a brilliant flash. Likewise, we think a brilliant solution starts with an arc. From concept to construction we deliver results for the long haul.</p>
      </div>
      <span class="brand">Heron Vessels, Inc.</span>
    </div>
    <div class="product-photos">
      <div class="photo ph-fittings" role="img" aria-label="Stack of stainless pipe fittings"></div>
      <div class="photo ph-pipes" role="img" aria-label="Fabricated pipe sections in the shop"></div>
      <div class="photo ph-flange" role="img" aria-label="Machined steel flange"></div>
    </div>
  </section>
  <footer class="flyer-foot">
    <div class="call"><small>CALL US NOW</small><strong>555-014-2270</strong></div>
    <div class="contact">
      <span><svg viewBox="0 0 10 10"><path d="M5 0a3.5 3.5 0 0 0-3.5 3.5C1.5 6 5 10 5 10s3.5-4 3.5-6.5A3.5 3.5 0 0 0 5 0zm0 5a1.5 1.5 0 1 1 0-3 1.5 1.5 0 0 1 0 3z"/></svg>410 North Ridge Rd Ashford, UT 84000</span>
      <span><i class="dot"></i>www.heronvesselsinc.example</span>
    </div>
  </footer>
</article>
</div>

<!-- ===== Bi-fold card, outside ===== -->
<div class="slot slot--card-out">
<article class="card">
  <div class="card-panel panel--black">
    <div class="card-foot">
      <span class="brand brand--light">Heron Vessels, Inc.</span>
      <div class="row">
        <div class="call"><small>CALL US NOW</small><strong>555-014-2270</strong></div>
        <div class="contact">
          <span><svg viewBox="0 0 10 10"><path d="M5 0a3.5 3.5 0 0 0-3.5 3.5C1.5 6 5 10 5 10s3.5-4 3.5-6.5A3.5 3.5 0 0 0 5 0zm0 5a1.5 1.5 0 1 1 0-3 1.5 1.5 0 0 1 0 3z"/></svg>410 North Ridge Rd Ashford, UT 84000</span>
          <span><i class="dot"></i>www.heronvesselsinc.example</span>
        </div>
      </div>
    </div>
  </div>
  <div class="card-panel panel--cover">
    <span class="brand">Heron Vessels, Inc.</span>
    <div class="cover-base"></div>
    <div class="cover-stripes"></div>
  </div>
</article>
</div>

<!-- ===== Bi-fold card, inside ===== -->
<div class="slot slot--card-in">
<article class="card card-inside">
  <div class="card-panel inside-left">
    <h2>Capabilities</h2>
    <div class="mini-cols">
      <ul class="tick-list">
        <li>Horizontal Lathes</li><li>Vertical Lathes</li><li>Horizontal Boring Mill Capabilities</li><li>Press Brake</li><li>Iron Workers</li><li>Band Saws</li><li>CNC Plasma Cutting</li><li>CNC Roll Forming</li>
      </ul>
      <ul class="tick-list">
        <li>Facility</li><li>Welding Processes</li><li>Paint &amp; Corrosion Control</li><li>Sandblasting</li><li>Insulating Systems</li><li>Hydraulic Assemblies</li><li>Drivelines</li>
      </ul>
    </div>
    <div class="inside-lower">
      <div class="special-box">
        <h4>SPECIALTIES</h4>
        <ul class="tick-list">
          <li>Tanks</li><li>Piping</li><li>Firetubes</li><li>Walkways &amp; Stairs</li><li>Pump Skids</li><li>Trailer Components</li><li>Tank Vents Clarifiers</li>
        </ul>
      </div>
      <div class="inside-photos">
        <div class="photo ph-sparks" role="img" aria-label="Laser cutting sparks"></div>
        <div class="photo ph-weld" role="img" aria-label="Welder at work"></div>
      </div>
    </div>
  </div>
  <div class="card-panel inside-right">
    <h2>OUR <b>PRODUCT</b></h2>
    <ul class="tick-list">
      <li>Tanks</li><li>Piping</li><li>Machining</li><li>Walkway &amp; Stairs</li><li>Tank Liner Systems</li><li>Insulation</li>
    </ul>
    <div class="cert-strip"><i></i><i></i><i></i><i></i></div>
    <div class="idea">
      <h3>A brilliant idea materialized...</h3>
      <p>It is said great ideas start with a brilliant flash. Likewise, we think a brilliant solution starts with an arc. From concept to construction we deliver results for the long haul.</p>
    </div>
    <div class="inside-pair">
      <div class="photo ph-fittings" role="img" aria-label="Stack of stainless pipe fittings"></div>
      <div class="photo ph-flange" role="img" aria-label="Machined steel flange"></div>
    </div>
    <div class="inside-sign"><span class="brand">Heron Vessels, Inc.</span><small>www.heronvesselsinc.example</small></div>
  </div>
</article>
</div>

<p class="board-label label--full-front">SIZE 1(FRONT)</p>
<p class="board-label label--full-back">SIZE 1(BACK)</p>
<p class="board-label label--half-front">SIZE 2(FRONT)</p>
<p class="board-label label--half-back">SIZE 2(BACK)</p>
<p class="board-label label--card">BUSINESS CARD</p>
<p class="board-label label--card-out">SIZE 3</p>
<p class="board-label label--card-in">SIZE 3</p>

</main>
</body>
</html>
```